Personal Web page for recruiter and owner of consulting firm

I work full time as a recruiter so I want a page that allows for me to support my efforts. I would like a long single page, I need to be able to upload four two minute videos, and 4 images. I also want the color scheme to match with my consulting company. I own the domain marcusfenwold.net already through wordpress . I took a shot at it myself and its terrible.

Target Market(s)

Potential clients

Industry/Entity Type

Management Consulting

Logo Text

marcus fenwold

Font styles to use
Serif

Requirements
Must have
• Must in color scheme go well with my consulting company logo attached
• Must be able to upload 4 two minute videos and 4 images (photos of me)
• Single long scroll page
• Modern and clean
Nice to have
• Easy for me to update videos images and text without complex coding
Should not have
• I want the design and feel to go well with my logos not exactly replicate it

```html
<!DOCTYPE html>
<html lang="en">
<head>
<meta charset="utf-8">
<title>Fenwold Strategies — Marcus Fenwold</title>
<link href="https://fonts.googleapis.com/css2?family=Exo+2:wght@300;400;500;600&family=Open+Sans:wght@400;600;700&family=Noto+Serif:ital@1&display=swap" rel="stylesheet">
<style>
:root{
  --blue:#2f4b8c;
  --blue-dark:#27407a;
  --ink:#3a3a3a;
  --text:#666;
  --dark:#41423f;
  --dark-2:#3c3d3b;
  --darkest:#333432;
  --line:#5a5b58;
  --white:#fff;
  --muted:#b7b8b4;
}
*{box-sizing:border-box;margin:0;padding:0}
html,body{width:1200px;height:2995px;overflow:hidden}
body{position:relative;background:var(--white);font-family:"Open Sans",sans-serif;color:var(--text)}

/* header */
.site-header{position:absolute;left:0;top:0;width:1200px;height:80px;background:var(--white)}
.brand{position:absolute;left:100px;top:25px;display:flex;align-items:center;gap:10px;font-family:"Exo 2",sans-serif;font-weight:400;color:var(--ink);font-size:24px;line-height:30px;white-space:nowrap}
.brand i{display:block;width:14px;height:14px;background:var(--blue)}
.nav{position:absolute;right:104px;top:36px;display:flex;gap:26px;font-size:12.5px;color:#333;text-transform:uppercase}
.nav .active{color:var(--blue)}
.nav-pointer{position:absolute;left:611px;top:72px;width:0;height:0;border-left:7px solid transparent;border-right:7px solid transparent;border-bottom:8px solid var(--blue)}

/* hero */
.hero{position:absolute;left:0;top:80px;width:1200px;height:508px;background:linear-gradient(100deg,#6b5a4a 0%,#8a8f98 30%,#b9c2cc 55%,#d9dde2 80%,#c8ccd2 100%)}
.hero-shade{position:absolute;inset:0;background:linear-gradient(90deg,rgba(40,45,55,.15),rgba(40,45,55,.35))}
.hero h1{position:absolute;left:590px;top:212px;width:540px;text-align:center;font-family:"Exo 2",sans-serif;font-weight:400;font-size:35px;line-height:44px;color:var(--white)}
.btn{display:inline-block;border-radius:16px;font-size:12px;text-transform:uppercase;text-align:center}
.hero .apply{position:absolute;left:710px;top:325px;width:140px;height:32px;line-height:28px;border:2px solid var(--white);color:var(--white)}
.hero .more{position:absolute;left:861px;top:325px;width:140px;height:32px;line-height:32px;background:var(--blue);color:var(--white)}

/* notch dividers */
.notch{position:absolute;left:576px;width:48px;height:22px}

/* welcome */
.welcome{position:absolute;left:0;top:588px;width:1200px;height:308px}
.section-title{position:absolute;left:0;width:1200px;text-align:center;font-family:"Exo 2",sans-serif;font-weight:300;font-size:22px;text-transform:uppercase;color:#444}
.section-title b{font-weight:500}
.welcome .section-title{top:50px}
.welcome .lead{position:absolute;left:150px;top:106px;width:900px;text-align:center;font-size:12.5px;font-weight:700;color:#333;text-transform:uppercase}
.welcome p.body{position:absolute;left:162px;top:142px;width:876px;text-align:center;font-size:10.5px;line-height:20px;color:#777}
.welcome .read{position:absolute;left:531px;top:227px;width:138px;height:32px;line-height:32px;background:var(--blue);color:var(--white)}

/* services */
.services{position:absolute;left:0;top:896px;width:1200px;height:624px;background:radial-gradient(circle at 360px 80px,#7a6a34 0,#4a4a40 200px,var(--dark) 360px)}
.services .section-title{top:64px;color:var(--white)}
.card{position:absolute;top:146px;width:296px;height:350px}
.card h3{height:54px;line-height:54px;text-align:center;font-family:"Exo 2",sans-serif;font-weight:500;font-size:23px;color:var(--white);text-transform:uppercase}
.card .photo{height:296px}
.card.staffing{left:146px}
.card.staffing h3{background:#4a4b48}
.card.staffing .photo{background:linear-gradient(160deg,#8a7062,#5d5450);position:relative}
.card.staffing .overlay{position:absolute;inset:0;background:rgba(70,70,70,.72);padding:88px 26px 0;text-align:center;color:var(--white)}
.card.staffing .overlay h4{font-size:13px;font-weight:700;text-transform:uppercase;margin-bottom:12px}
.card.staffing .overlay p{font-size:10.5px;line-height:20px}
.card.consulting{left:452px}
.card.consulting h3,.card.employment h3{background:var(--blue)}
.card.consulting .photo{background:linear-gradient(150deg,#d8d4cf,#a99a8f 50%,#ece9e6)}
.card.employment{left:758px}
.card.employment .photo{background:linear-gradient(150deg,#e8e8e6,#8b8c92 50%,#dfe0e2)}

/* videos */
.videos{position:absolute;left:0;top:1520px;width:1200px;height:474px}
.videos .section-title{top:64px}
.video{position:absolute;top:112px;width:248px;height:296px}
.video .play{position:absolute;left:106px;top:130px}
.v1{left:100px;background:linear-gradient(160deg,#b7c3cf,#2e3f5c)}
.v2{left:351px;background:linear-gradient(160deg,#8b8070,#c2c9bf)}
.v3{left:602px;background:linear-gradient(160deg,#8f9aa3,#3f4853)}
.v4{left:853px;background:linear-gradient(160deg,#8a8c86,#a9b4c6)}

/* testimonials */
.testimonials{position:absolute;left:0;top:1994px;width:1200px;height:466px;background:radial-gradient(ellipse at 30% 40%,#76736e,#5e5c58 60%,#4c4b48)}
.testimonials .section-title{top:72px;color:var(--white)}
.testimonials .sub{position:absolute;left:0;top:112px;width:1200px;text-align:center;font-size:10.5px;color:#e6e6e6}
.quote{position:absolute;top:168px;width:488px;height:172px;padding:42px 0 0 158px}
.quote.light{left:116px;background:var(--white)}
.quote.plain{left:580px;padding-left:206px;padding-top:30px}
.avatar{position:absolute;left:34px;top:30px;width:82px;height:82px;border-radius:50%}
.quote.light .avatar{background:linear-gradient(160deg,#b8744c,#e4c8b4)}
.quote.plain .avatar{left:90px;top:22px;width:68px;height:68px;background:linear-gradient(160deg,#6e4a38,#d9b7a0)}
.qmark{position:absolute;left:96px;top:78px;width:34px;height:34px;border-radius:50%;background:var(--blue);color:var(--white);text-align:center;font-family:"Noto Serif",serif;font-size:28px;line-height:40px}
.quote.plain .qmark{left:144px;top:66px;background:var(--white);color:#777}
.quote h5{font-size:11px;font-weight:700;color:var(--blue);text-transform:uppercase}
.quote.plain h5{color:var(--white)}
.quote .mail{font-size:9.5px;color:var(--blue);font-weight:600;margin-bottom:10px}
.quote.plain .mail{color:var(--white)}
.quote p{font-family:"Noto Serif",serif;font-style:italic;font-size:11.5px;line-height:20px;color:#666;width:300px}
.quote.plain p{color:#eee}
.dots{position:absolute;left:576px;top:404px;display:flex;gap:5px}
.dots i{width:6px;height:6px;border-radius:50%;background:#ddd;display:block}

/* cta */
.cta{position:absolute;left:0;top:2460px;width:1200px;height:118px;background:var(--blue)}
.cta h2{position:absolute;left:196px;top:40px;font-family:"Exo 2",sans-serif;font-weight:400;font-size:25px;letter-spacing:1.5px;color:var(--white);text-transform:uppercase}
.cta .contact{position:absolute;left:812px;top:32px;width:170px;height:46px;line-height:46px;background:var(--white);color:var(--blue-dark);font-size:15px;font-weight:600;text-align:center;border-radius:3px}
.diamond{position:absolute;left:583px;top:-17px;width:34px;height:34px;background:var(--white);transform:rotate(45deg)}
.diamond-plus{position:absolute;left:583px;top:-17px;width:34px;height:34px;line-height:34px;text-align:center;color:var(--blue);font-size:18px}

/* footer */
.footer{position:absolute;left:0;top:2578px;width:1200px;height:382px;background:var(--dark-2);color:var(--muted)}
.col{position:absolute;top:38px;width:232px}
.col h6{font-size:13.5px;font-weight:600;color:var(--white);text-transform:uppercase;margin-bottom:18px}
.col p{font-size:10px;line-height:18px}
.about{left:100px}
.info{margin-top:16px;padding-left:30px;position:relative;font-size:10px;line-height:16px}
.info svg{position:absolute;left:0;top:2px}
.info b{color:var(--white);font-weight:600;display:block}
.news{left:356px}
.news-item{position:relative;height:86px;border-bottom:1px solid var(--line);padding-left:70px}
.news-item .thumb{position:absolute;left:0;top:8px;width:52px;height:44px;background:linear-gradient(150deg,#b9bec6,#5a6272)}
.news-item h4{padding-top:6px;font-size:11.5px;font-weight:700;color:#ddd;line-height:20px}
.news-item span{font-size:9px}
.svc{left:614px}
.svc ul{list-style:none}
.svc li{font-size:10.5px;height:41px;line-height:36px;border-bottom:1px dashed var(--line)}
.svc li::before{content:"› "}
.svc li.on{color:var(--white)}
.nl{left:870px}
.nl .field{display:flex;height:32px}
.nl .field div{width:200px;background:#eee;color:#888;font-size:10px;line-height:32px;padding-left:10px}
.nl .field span{width:32px;background:var(--blue);display:flex;align-items:center;justify-content:center}
.nl .mark{margin-top:24px;margin-left:16px;display:flex;align-items:center;gap:9px;font-family:"Exo 2",sans-serif;font-weight:400;font-size:22px;color:var(--white);line-height:28px;white-space:nowrap}
.nl .mark i{display:block;width:12px;height:12px;background:var(--white)}
.nl p{margin-top:14px}
.social{display:flex;gap:18px;margin-top:30px;padding-left:12px}
.social i{width:10px;height:10px;border-radius:50%;background:#cfcfcf;display:block}
.copy{position:absolute;left:0;top:2960px;width:1200px;height:35px;background:var(--darkest);text-align:center;font-size:9.5px;line-height:35px;color:var(--muted)}
</style>
</head>
<body>

<header class="site-header">
  <div class="brand"><i></i>Fenwold Strategies</div>
  <nav class="nav">
    <span class="active">Home</span><span>About Us</span><span>Services</span><span>Videos</span><span>Testimonials</span><span>Contact Us</span>
  </nav>
  <div class="nav-pointer"></div>
</header>

<section class="hero">
  <div role="img" aria-label="Smiling recruiter in a suit in front of colleagues meeting in a bright office" style="position:absolute;inset:0"></div>
  <div class="hero-shade"></div>
  <h1>We are a full time recruiter and own a consulting firm</h1>
  <span class="btn apply">Apply Now</span>
  <span class="btn more">Learn More</span>
</section>
<svg class="notch" style="top:566px" width="48" height="22" viewBox="0 0 48 22"><polygon points="0,22 24,0 48,22" fill="#fff"/><text x="24" y="19" text-anchor="middle" font-size="14" fill="#777">+</text></svg>

<section class="welcome">
  <h2 class="section-title">Welcome to <b>Fenwold Strategies</b></h2>
  <p class="lead">Bulum iaculis lacinia est. Proin dictum elemntum velit. Fusce euismod consequat antrem ipsum dolor.</p>
  <p class="body">Bulum iaculis lacinia est. Proin dictum elemntum velit. Fusce euismod consequat ante. Lorem ipsum dolor sit met consectetuer adipiscing elit. ellentesque sed dolor. Aliquam congue fermentum nisl. Mauris accsan nulla vel diam. Sed in lacus ut enim adipiscing aliquetulla vene natis. In pede mi aliquet sit amet euismod inuctor ut ligula. Aliquam dapibus tincidunt metus. Praesent justo dolo.</p>
  <span class="btn read">Read More</span>
</section>

<section class="services">
  <svg class="notch" style="top:0" width="48" height="22" viewBox="0 0 48 22"><polygon points="0,0 24,22 48,0" fill="#fff"/><text x="24" y="12" text-anchor="middle" font-size="14" fill="#777">+</text></svg>
  <h2 class="section-title">Our <b>Services</b></h2>
  <article class="card staffing">
    <h3>Staffing</h3>
    <div class="photo" role="img" aria-label="Team of colleagues at work">
      <div class="overlay">
        <h4>Vestibulum iaculis laci</h4>
        <p>Bulum iaculis lacinia est. Proin dictum elemntum velit. Fusce euismod consequat ante. Lorem ipsum dolsit met consetuer adipiscing elit llen-tesque sed dolor. Aliquam congue fermsl. Mauri-accumsan nulla vel diam. Sed in lacus ut enim adipiscing aliquetulla vene natis. In pede mi aliquet sit amet euismod in.</p>
      </div>
    </div>
  </article>
  <article class="card consulting">
    <h3>Consulting</h3>
    <div class="photo" role="img" aria-label="Two smiling businesswomen in a consulting meeting"></div>
  </article>
  <article class="card employment">
    <h3>Employment</h3>
    <div class="photo" role="img" aria-label="Businessman and businesswoman reviewing a document folder"></div>
  </article>
  <svg class="notch" style="top:602px" width="48" height="22" viewBox="0 0 48 22"><polygon points="0,22 24,0 48,22" fill="#fff"/><text x="24" y="19" text-anchor="middle" font-size="14" fill="#777">+</text></svg>
</section>

<section class="videos">
  <h2 class="section-title">Our <b>Videos</b></h2>
  <div class="video v1" role="img" aria-label="Video thumbnail: two businessmen talking at a table">
    <svg class="play" width="36" height="36" viewBox="0 0 36 36"><circle cx="18" cy="18" r="18" fill="#111"/><polygon points="14,11 25,18 14,25" fill="#fff"/></svg>
  </div>
  <div class="video v2" role="img" aria-label="Video thumbnail: interview between two people">
    <svg class="play" width="36" height="36" viewBox="0 0 36 36"><circle cx="18" cy="18" r="18" fill="#111"/><polygon points="14,11 25,18 14,25" fill="#fff"/></svg>
  </div>
  <div class="video v3" role="img" aria-label="Video thumbnail: man with a headset at a desk">
    <svg class="play" width="36" height="36" viewBox="0 0 36 36"><circle cx="18" cy="18" r="18" fill="#111"/><polygon points="14,11 25,18 14,25" fill="#fff"/></svg>
  </div>
  <div class="video v4" role="img" aria-label="Video thumbnail: businessman with crossed arms">
    <svg class="play" width="36" height="36" viewBox="0 0 36 36"><circle cx="18" cy="18" r="18" fill="#111"/><polygon points="14,11 25,18 14,25" fill="#fff"/></svg>
  </div>
</section>

<section class="testimonials">
  <div role="img" aria-label="Background of smooth grey river stones" style="position:absolute;inset:0"></div>
  <svg class="notch" style="top:0" width="48" height="22" viewBox="0 0 48 22"><polygon points="0,0 24,22 48,0" fill="#fff"/><text x="24" y="12" text-anchor="middle" font-size="14" fill="#777">+</text></svg>
  <h2 class="section-title">Testimonials</h2>
  <p class="sub">Neque porro quisquam est qui dolorem ipsum quia dolor sit amet,</p>
  <div class="quote light">
    <div class="avatar" role="img" aria-label="Portrait of client"></div>
    <div class="qmark">“</div>
    <h5>Nora Pell</h5>
    <div class="mail">info@fenwoldmail.net</div>
    <p>Natus voluptatum enim quod necessitatibus quis expedita harum provident eos obcaecati id culpa corporis molestias.</p>
  </div>
  <div class="quote plain">
    <div class="avatar" role="img" aria-label="Portrait of client"></div>
    <div class="qmark">“</div>
    <h5>Evan Ruiz</h5>
    <div class="mail">info@fenwoldmail.net</div>
    <p>Natus voluptatum enim quod necessitatibus quis expedita harum provident eos obcaecati id culpa corporis molestias.</p>
  </div>
  <div class="dots"><i></i><i></i><i></i><i></i></div>
</section>

<section class="cta">
  <div class="diamond"></div><div class="diamond-plus">+</div>
  <h2>Neque porro quisquam est qui dolorem</h2>
  <span class="contact">Contact Us</span>
</section>

<footer class="footer">
  <div class="col about">
    <h6>About Us</h6>
    <p>Lorem ipsum dolor sit amet consec tetur adipiscing elit nulla aliquet pretium nisi in cursus maecenas nec eleifen.</p>
    <div class="info">
      <svg width="12" height="12" viewBox="0 0 12 12"><polygon points="11,1 1,5 5,6 6,11" fill="#fff"/></svg>
      <b>Location</b>123 suscipit ipsum nam auctor mauris dui, ac sollicitudin mauris, Lakeview
    </div>
    <div class="info">
      <svg width="12" height="12" viewBox="0 0 12 12"><path d="M3 1l2 3-1.5 1.5a7 7 0 0 0 3 3L8 7l3 2-1 2C5 11 1 7 1 2z" fill="#fff"/></svg>
      <b>Phone :</b>+1 5550 1234
    </div>
    <div class="info">
      <svg width="12" height="12" viewBox="0 0 12 12"><rect x="1" y="2.5" width="10" height="7" fill="none" stroke="#fff"/><polyline points="1,2.5 6,7 11,2.5" fill="none" stroke="#fff"/></svg>
      <b>Email Address :</b>hello@fenwoldmail.net
    </div>
  </div>

  <div class="col news">
    <h6>Latest News</h6>
    <div class="news-item"><div class="thumb" role="img" aria-label="News photo"></div><h4>Lorem ipsum dolor sit amet, consectetur</h4><span>27th July 2015</span></div>
    <div class="news-item"><div class="thumb" role="img" aria-label="News photo"></div><h4>Lorem ipsum dolor sit amet, consectetur</h4><span>27th July 2015</span></div>
    <div class="news-item"><div class="thumb" role="img" aria-label="News photo"></div><h4>Lorem ipsum dolor sit amet, consectetur</h4><span>27th July 2015</span></div>
  </div>

  <div class="col svc">
    <h6>Our Services</h6>
    <ul><li>Staffing</li><li>Employment</li><li>Consulting</li><li class="on">Management</li><li>Support</li><li>Forums</li></ul>
  </div>

  <div class="col nl">
    <h6>Newsletter</h6>
    <div class="field"><div>Enter you Email</div><span><svg width="10" height="10" viewBox="0 0 10 10"><polygon points="2,1 8,5 2,9" fill="#fff"/></svg></span></div>
    <div class="mark"><i></i>Fenwold Strategies</div>
    <p>Lorem ipsum dolor sit amet consec tetur adipiscing elit nulla aliquet pretium nisi</p>
    <div class="social"><i></i><i></i><i></i><i></i><i></i><i></i></div>
  </div>
</footer>
<div class="copy">Copyrights © 2017 - All Rights Reserved</div>

</body>
</html>
```